Larkfield & Stonemason Valtorra Cargoline 4200

Need to create a wrap that really POPS. The customer is a home contractor. His website is https://larkfieldstonemason.com/
He wants the wrap to capture everything he creates. The work truck is a 2012 Valtorra Cargoline box truck 3500. The box is 12ft wide x 86" tall. The rear door is 70" tall x 70" wide. He wants to incorporate red/gray/black into the logo and design. Also, he likes the attached wrap design. Use that for inspiration, please do not copy directly.

```html
<!DOCTYPE html>
<html lang="en">
<head>
<meta charset="utf-8">
<title>Larkfield &amp; Stonemason – Box Truck Wrap</title>
<link rel="stylesheet" href="https://fonts.googleapis.com/css2?family=Archivo+Black&family=Encode+Sans+Semi+Condensed:wght@500;700&display=swap">
<style>
  :root {
    --page: #ececec;
    --panel: #e3e5e9;
    --door: #ffffff;
    --ink: #0b0b0b;
    --brand-red: #d71920;
    --band-gray: #8b8b8d;
    --band-brown: #4a2c27;
    --name-brown: #4a2a26;
    --white: #ffffff;
  }
  html, body {
    margin: 0;
    width: 1200px;
    height: 680px;
    overflow: hidden;
    background: var(--page);
  }
  .wrap-layout {
    position: absolute;
    left: 20px;
    top: 80px;
    width: 1160px;
    height: 520px;
    display: block;
  }
  .heavy { font-family: "Archivo Black", "Arial Black", sans-serif; }
  .cond  { font-family: "Encode Sans Semi Condensed", "Arial Narrow", sans-serif; }
  .tagline     { fill: var(--white); font-weight: 500; }
  .phone-text  { fill: var(--brand-red); font-weight: 700; }
  .door-phone  { fill: var(--white); font-weight: 700; }
  .motto       { fill: var(--white); font-weight: 500; }
  .brand-name  { fill: var(--name-brown); }
  .service-head{ fill: var(--ink); }
  .license     { fill: var(--ink); font-weight: 700; }
  .web-address { fill: var(--white); stroke: var(--ink); stroke-width: 3; paint-order: stroke; }
  .door-web    { fill: var(--white); }
  .service-list{ fill: var(--white); font-weight: 500; }
</style>
</head>
<body>
<svg class="wrap-layout" viewBox="180 200 2210 990" xmlns="http://www.w3.org/2000/svg">
  <defs>
    <symbol id="phone-icon" viewBox="0 0 44 44">
      <path d="M12 11 q3 -3 6 0 l3 5 q1 3 -2 5 q3 6 9 9 q2 -3 5 -2 l5 3 q3 3 0 6 l-3 3 q-8 2 -18 -8 q-10 -10 -8 -18 z" fill="currentColor"/>
    </symbol>
  </defs>

  <!-- ===== Cab door panel ===== -->
  <g class="door-panel">
    <rect class="door-base" x="180" y="800" width="710" height="235" fill="var(--door)"/>
    <rect class="door-band-red" x="430" y="1035" width="460" height="68" fill="var(--brand-red)"/>
    <rect class="door-band-black" x="470" y="1103" width="420" height="72" fill="var(--ink)"/>

    <text class="cond license" x="285" y="930" font-size="14" text-anchor="middle" letter-spacing="1.5" font-weight="500">LICENSE NUMBER</text>
    <text class="cond license" x="285" y="951" font-size="19" text-anchor="middle">13LS04417000</text>

    <rect class="brand-mark" x="652" y="838" width="22" height="16" fill="var(--brand-red)"/>
    <text class="heavy brand-name" x="662" y="898" font-size="28" text-anchor="middle">LARKFIELD &amp;</text>
    <text class="heavy brand-name" x="662" y="950" font-size="38" text-anchor="middle" textLength="330" lengthAdjust="spacingAndGlyphs">STONEMASON</text>
    <text class="heavy service-head" x="662" y="990" font-size="31" text-anchor="middle" textLength="255" lengthAdjust="spacingAndGlyphs">REMODELING</text>
    <text class="heavy service-head" x="662" y="1012" font-size="15" text-anchor="middle" textLength="340" lengthAdjust="spacingAndGlyphs">KITCHEN | BATHROOM | HOME REPAIR</text>

    <text class="heavy door-web" x="662" y="1077" font-size="15" text-anchor="middle" textLength="365" lengthAdjust="spacing">WWW.LARKFIELDSTONEMASON.COM</text>

    <circle cx="552" cy="1135" r="14" fill="var(--white)"/>
    <use href="#phone-icon" x="539" y="1122" width="26" height="26" color="var(--ink)"/>
    <text class="cond door-phone" x="572" y="1144" font-size="27">(555) 214-8630</text>
  </g>

  <!-- ===== Box side panel ===== -->
  <g class="box-panel" transform="translate(950 220)">
    <rect class="panel-base" width="1420" height="765" fill="var(--panel)"/>

    <polygon class="band-gray" points="440,0 1420,0 1420,600" fill="var(--band-gray)"/>
    <polygon class="band-brown" role="img" aria-label="Textured wood-grain accent band" points="470,0 1420,0 1420,575" fill="var(--band-brown)"/>
    <polygon class="corner-black" points="610,0 1420,0 1420,492" fill="var(--ink)"/>

    <rect class="band-red" x="0" y="598" width="1420" height="82" fill="var(--brand-red)"/>
    <rect class="band-black" x="0" y="680" width="1420" height="85" fill="var(--ink)"/>

    <text class="cond tagline" x="1385" y="70" font-size="40" text-anchor="end">ALL YOUR CARPENTRY &amp; GENERAL</text>
    <text class="cond tagline" x="1385" y="112" font-size="31" text-anchor="end">CONSTRUCION NEEDS DESIGN &amp; BUILD</text>

    <g class="phone">
      <circle cx="1034" cy="198" r="22" fill="var(--brand-red)"/>
      <use href="#phone-icon" x="1012" y="176" width="44" height="44" color="var(--ink)"/>
      <text class="cond phone-text" x="1385" y="214" font-size="46" text-anchor="end">(555) 214-8630</text>
    </g>

    <text class="cond motto" x="1385" y="292" font-size="22" text-anchor="end">THE ONLY CORNER WE CUT</text>
    <text class="cond motto" x="1385" y="318" font-size="22" text-anchor="end">IS MITER CORNER</text>

    <rect class="brand-mark" x="462" y="180" width="54" height="36" fill="var(--brand-red)"/>
    <text class="heavy brand-name" x="487" y="290" font-size="64" text-anchor="middle">LARKFIELD &amp;</text>
    <text class="heavy brand-name" x="487" y="402" font-size="96" text-anchor="middle" textLength="870" lengthAdjust="spacingAndGlyphs">STONEMASON</text>

    <text class="heavy service-head" x="487" y="505" font-size="74" text-anchor="middle" textLength="670" lengthAdjust="spacingAndGlyphs">REMODELING</text>
    <text class="heavy service-head" x="487" y="560" font-size="40" text-anchor="middle" textLength="900" lengthAdjust="spacingAndGlyphs">KITCHEN | BATHROOM | HOME REPAIR</text>

    <text class="cond license" x="1115" y="528" font-size="20" text-anchor="middle" letter-spacing="2" font-weight="500">LICENSE NUMBER</text>
    <text class="cond license" x="1115" y="558" font-size="29" text-anchor="middle">13LS04417000</text>

    <text class="heavy web-address" x="35" y="662" font-size="60" textLength="1350" lengthAdjust="spacing">WWW.LARKFIELDSTONEMASON.COM</text>

    <text class="cond service-list" x="38" y="724" font-size="26" textLength="1350" lengthAdjust="spacingAndGlyphs">INTERIOR REMODELING | KITCHEN REMODELING | CUSTOM DECKS | FINISH CARPENTRY | HOME ADDITIONS | WINDOWS &amp; DOORS</text>
  </g>
</svg>
</body>
</html>
```